we can communicate on this, but i want to follow the approach we took on Pellew|Marsh & Quinlan but i feel the card front needs the black background and the platinum and gold logo. The back? I am open. we can use the same info from PM&Q. Velmont Arc is an enhanced equity investment fund - basically a very exclusive boutique hedge fund that uses only stock options. very advanced things. hope you are interested

Contact Information for Business Card

Dr. Lewis T. Brennick, CFA
Scientifique de fusée financière
701.555.0143
LTBquant47@mailvantor.com

4718 Willow Creek Bend W.
West Fargo, ND 58078

No web site

Colors

Designer to choose colors to be used in the design.

Requirements
Nice to have
• I tend to prefer the most visible applications of the logo to include logo and name, the logo version with a black background and the gold and platinum components separated by the black. I see this working well for a single side (logo and name - this is card front to me).
• I am fairly open to other treatments on the reverse side with the data. To me, it makes sense to have a different color rendition of the logo on the reverse and it may be a muted black tone on tone or an oversized portion that would have spot UV. Or, the reverse may play with colors and layout
Should not have
• Other colors = no no
• Decorative font

```html
<!DOCTYPE html>
<html lang="en">
<head>
<meta charset="utf-8">
<title>Velmont Arc – Business Card</title>
<link href="https://fonts.googleapis.com/css2?family=Roboto:wght@400;500&display=swap" rel="stylesheet">
<style>
  :root {
    --backdrop: #1d1d1d;
    --card: #141516;
    --card-edge: #202224;
    --platinum: #c9cacc;
    --platinum-dark: #6f7174;
    --gold: #d6a92c;
    --ink-light: #f2f2f2;
  }
  * { margin: 0; padding: 0; box-sizing: border-box; }
  html, body {
    width: 1200px; height: 800px; overflow: hidden;
    background: var(--backdrop);
    font-family: "Roboto", Arial, sans-serif;
  }
  .canvas {
    width: 1200px; height: 800px;
    display: flex; align-items: center; justify-content: center; gap: 40px;
  }
  .card {
    position: relative;
    width: 520px; height: 300px;
    background: linear-gradient(160deg, var(--card-edge) 0%, var(--card) 70%);
    border-radius: 16px;
    box-shadow: 0 10px 30px rgba(0,0,0,.45);
  }
  /* Front */
  .card-front {
    display: flex; flex-direction: column; align-items: center; justify-content: center; gap: 18px;
  }
  .brand-mark {
    width: 96px; height: 96px; border-radius: 50%;
    background: var(--platinum-dark);
  }
  .brand-name {
    font-weight: 500; font-size: 40px; letter-spacing: 4px;
    text-transform: uppercase; color: var(--platinum);
  }
  /* Back */
  .holder {
    position: absolute; top: 34px; right: 34px; text-align: right;
  }
  .holder-name {
    color: var(--gold); font-weight: 500; font-size: 22px;
  }
  .holder-name .prefix, .holder-name .credential { font-size: 14px; }
  .holder-title {
    color: var(--ink-light); font-size: 13px; margin-top: 3px;
  }
  .contact {
    position: absolute; left: 34px; bottom: 30px;
    color: var(--ink-light); font-size: 13px; line-height: 1.45;
  }
  .address { margin-bottom: 12px; }
  .contact-list { list-style: none; }
  .contact-list li { display: flex; align-items: center; gap: 8px; }
  .contact-list svg { width: 12px; height: 12px; flex: none; }
</style>
</head>
<body>
<main class="canvas">
  <section class="card card-front" aria-label="Card front">
    <div class="brand-mark"></div>
    <div class="brand-name">Velmont Arc</div>
  </section>

  <section class="card card-back" aria-label="Card back">
    <div class="holder">
      <div class="holder-name"><span class="prefix">Dr.</span> Lewis T. Brennick, <span class="credential">CFA</span></div>
      <div class="holder-title">Scientifique des Fusées Financières</div>
    </div>
    <div class="contact">
      <div class="address">4718 Willow Creek Bend W.<br>West Fargo, ND 58078</div>
      <ul class="contact-list">
        <li>
          <svg viewBox="0 0 12 12" aria-hidden="true"><rect x="3" y="0.8" width="6" height="10.4" rx="1" fill="none" stroke="var(--gold)" stroke-width="1.3"/><line x1="5" y1="9.4" x2="7" y2="9.4" stroke="var(--gold)" stroke-width="1"/></svg>
          701.555.0143
        </li>
        <li>
          <svg viewBox="0 0 12 12" aria-hidden="true"><rect x="0.5" y="2.5" width="11" height="7.5" fill="var(--gold)"/><polyline points="0.5,2.5 6,7 11.5,2.5" fill="none" stroke="var(--card)" stroke-width="1"/></svg>
          LTBquant47@mailvantor.com
        </li>
      </ul>
    </div>
  </section>
</main>
</body>
</html>
```